Torvane Halbridge

Looking for modern business cards.
Clean contemporary design.
Similar to this.
https://www.plumvexa-search.example/imgres?imgurl=https%3A%2F%2Fimg.quorlint-cdn.example%2Fsleek_dark_metal_card_design_540.jpg&imgrefurl=https%3A%2F%2Fwww.quorlint-prints.example%2Fsleek_dark_metal_card_design-918273645501928374&q=modern%20business%20cards

But I'd like the blue to look metallic.

Business

```html
<!DOCTYPE html>
<html lang="en">
<head>
<meta charset="utf-8">
<title>Torvane Halbridge – Business Cards</title>
<link rel="stylesheet" href="https://fonts.googleapis.com/css2?family=Open+Sans:wght@400;600;700&display=swap">
<style>
  :root {
    --backdrop: #8c8c8c;
    --card-dark: #141414;
    --card-mid: #242424;
    --metal-blue: #3a94bb;
    --metal-blue-light: #bfe6f5;
    --metal-blue-deep: #1b5a78;
    --steel-light: #ffffff;
    --steel-deep: #8d8d8d;
    --white: #ffffff;
    --rule: #9a9a9a;
  }
  html, body {
    margin: 0;
    padding: 0;
    width: 1200px;
    height: 900px;
    overflow: hidden;
    background: var(--backdrop);
    font-family: "Open Sans", Arial, sans-serif;
  }
  .canvas {
    position: relative;
    width: 1200px;
    height: 900px;
  }
  .card {
    position: absolute;
    top: 170px;
    width: 347px;
    height: 561px;
    color: var(--white);
    background:
      repeating-linear-gradient(90deg,
        rgba(255,255,255,0.035) 0px, rgba(255,255,255,0.035) 1px,
        rgba(0,0,0,0.06) 1px, rgba(0,0,0,0.06) 2px,
        rgba(255,255,255,0.015) 2px, rgba(255,255,255,0.015) 4px,
        rgba(0,0,0,0.04) 4px, rgba(0,0,0,0.04) 5px),
      repeating-linear-gradient(90deg,
        rgba(255,255,255,0.025) 0px, rgba(255,255,255,0.025) 3px,
        transparent 3px, transparent 11px),
      linear-gradient(180deg, var(--card-mid) 0%, var(--card-dark) 100%);
  }
  .card--front { left: 259px; }
  .card--back {
    left: 631px;
    background:
      repeating-linear-gradient(90deg,
        rgba(255,255,255,0.03) 0px, rgba(255,255,255,0.03) 1px,
        rgba(0,0,0,0.07) 1px, rgba(0,0,0,0.07) 2px,
        rgba(255,255,255,0.012) 2px, rgba(255,255,255,0.012) 4px,
        rgba(0,0,0,0.05) 4px, rgba(0,0,0,0.05) 5px),
      repeating-linear-gradient(90deg,
        rgba(255,255,255,0.02) 0px, rgba(255,255,255,0.02) 3px,
        transparent 3px, transparent 13px),
      linear-gradient(180deg, #1c1c1c 0%, #111111 100%);
  }
  .brand {
    position: absolute;
    display: flex;
    align-items: center;
    gap: 10px;
    white-space: nowrap;
  }
  .brand__name {
    font-size: 27px;
    font-weight: 600;
    letter-spacing: -0.3px;
  }
  .brand__dot {
    width: 16px;
    height: 16px;
    border-radius: 50%;
  }
  .card--front .brand { left: 30px; top: 174px; }
  .card--front .brand__name { color: var(--metal-blue); }
  .card--front .brand__dot {
    background: radial-gradient(circle at 35% 30%, var(--metal-blue-light) 0%, var(--metal-blue) 45%, var(--metal-blue-deep) 100%);
  }
  .card--back .brand { left: 27px; top: 279px; }
  .card--back .brand__name { color: var(--white); }
  .card--back .brand__dot {
    background: radial-gradient(circle at 35% 30%, var(--steel-light) 0%, #dcdcdc 50%, var(--steel-deep) 100%);
  }
  .contact {
    position: absolute;
    left: 0;
    right: 0;
    top: 372px;
    text-align: center;
  }
  .contact__name {
    margin: 0;
    font-size: 23px;
    font-weight: 700;
    letter-spacing: 0.3px;
    line-height: 1.2;
  }
  .contact__role {
    margin: 0;
    font-size: 16px;
    font-weight: 400;
    line-height: 1.4;
  }
  .contact__rule {
    width: 177px;
    height: 1px;
    margin: 10px auto 12px;
    background: var(--rule);
    border: 0;
  }
  .contact__list {
    list-style: none;
    margin: 0;
    padding: 0;
    font-size: 16px;
    line-height: 24px;
  }
  .contact__label { font-weight: 700; }
  .contact__web { font-weight: 700; }
</style>
</head>
<body>
<main class="canvas">
  <section class="card card--front" aria-label="Card front">
    <div class="brand">
      <span class="brand__name">Torvane Halbridge</span>
      <span class="brand__dot"></span>
    </div>
    <div class="contact">
      <h1 class="contact__name">MAREN COSTELL</h1>
      <p class="contact__role">Managing Director</p>
      <hr class="contact__rule">
      <ul class="contact__list">
        <li><span class="contact__label">P:</span> 555-014-2387</li>
        <li><span class="contact__label">E:</span> hello@torvanehalbridge.example</li>
        <li class="contact__web">www.torvanehalbridge.example</li>
      </ul>
    </div>
  </section>
  <section class="card card--back" aria-label="Card back">
    <div class="brand">
      <span class="brand__name">Torvane Halbridge</span>
      <span class="brand__dot"></span>
    </div>
  </section>
</main>
</body>
</html>
```